Postcard Design Project A Healthy reminder

Dr.'s Dhelpit and Sirel dunwat. Internal Medicine/Family practice. This postcard will be for our patients that we have not seen in a while. Also we need another postcard (the one your designing) with a different heading for New patient's. Do you offer a price break for that? The only thing we would need to change is the heading. Please let me know. Thank you so much! Also can you use the map on the last postcard and our logo I made? I cant find it. Please feel free to call me or email me.

```html
<!DOCTYPE html>
<html lang="en">
<head>
<meta charset="utf-8">
<title>Annual Exam Reminder Postcard</title>
<link href="https://fonts.googleapis.com/css2?family=Open+Sans:wght@400;600;700;800&display=swap" rel="stylesheet">
<style>
  :root {
    --red: #b5060d;
    --red-dark: #8c0a10;
    --ink: #1c1c1c;
    --silver: #c9c9c9;
    --silver-dark: #8e8e8e;
    --paper: #ffffff;
    --mist: #f1f1f1;
    --stage: #6f6f6f;
  }
  * { margin: 0; padding: 0; box-sizing: border-box; }
  html, body { width: 880px; height: 1200px; overflow: hidden; }
  body {
    background: var(--stage);
    font-family: "Open Sans", sans-serif;
    position: relative;
  }
  .card {
    position: absolute;
    left: 58px;
    width: 764px;
    height: 519px;
    background: var(--paper);
    overflow: hidden;
  }
  .card-front { top: 61px; }
  .card-back { top: 624px; height: 520px; }
  .card-shapes { position: absolute; inset: 0; width: 100%; height: 100%; }

  /* front */
  .brand {
    position: absolute; left: 54px; top: 58px;
    display: flex; align-items: center; gap: 8px;
    font-weight: 700; font-size: 15px; color: var(--ink);
  }
  .brand-mark { width: 12px; height: 12px; background: var(--red); }
  .brand-tag {
    position: absolute; left: 82px; top: 83px;
    font-size: 8px; font-weight: 700; letter-spacing: 1px; color: var(--ink);
  }
  .headline {
    position: absolute; left: 47px; top: 168px;
    color: var(--ink); line-height: 1;
  }
  .headline-lead { font-size: 30px; font-weight: 400; letter-spacing: -0.5px; }
  .headline-lead strong { color: var(--red); font-weight: 800; }
  .headline-lead + .headline-lead { margin-top: 6px; }
  .headline-big {
    font-size: 86px; font-weight: 800; letter-spacing: -3px; line-height: 0.82;
  }
  .headline-big:first-of-type { margin-top: 4px; }
  .headline-big.red { color: var(--red); }
  .address {
    position: absolute; left: 50px; top: 450px;
    display: flex; gap: 10px; color: var(--paper);
    font-size: 17px; line-height: 24px;
  }
  .address svg { margin-top: 3px; }
  .contact {
    position: absolute; right: 56px; top: 440px; text-align: right; color: var(--paper);
  }
  .contact-phone {
    display: flex; align-items: center; justify-content: flex-end; gap: 10px;
    font-size: 30px; font-weight: 700; line-height: 36px;
  }
  .contact-web {
    display: flex; align-items: center; justify-content: flex-end; gap: 8px;
    font-size: 19px; margin-top: 4px;
  }
  .contact-web strong { font-weight: 700; }

  /* back */
  .doctors {
    position: absolute; left: 39px; top: 34px;
    font-size: 28px; line-height: 38px; font-weight: 800; color: var(--red);
  }
  .doctors span { font-weight: 400; color: var(--ink); }
  .cta {
    position: absolute; left: 38px; top: 291px;
    color: var(--paper); font-weight: 800; font-size: 27px; line-height: 28px;
  }
  .social {
    position: absolute; left: 260px; top: 298px; color: var(--paper);
  }
  .social-line {
    display: flex; align-items: center; gap: 6px; font-weight: 800; font-size: 13px;
  }
  .social-dot { width: 17px; height: 17px; border-radius: 50%; background: #3b5ea8; }
  .social-note { font-size: 8.5px; font-weight: 700; line-height: 12px; margin-top: 6px; }
  .stamp {
    position: absolute; left: 629px; top: 38px; width: 91px; height: 90px;
    border: 1px solid #777;
  }
  .address-line {
    position: absolute; left: 479px; width: 240px; height: 1px; background: #555;
  }
</style>
</head>
<body>

<section class="card card-front">
  <svg class="card-shapes" viewBox="0 0 764 519" aria-hidden="true">
    <defs>
      <linearGradient id="frontPaper" x1="0" y1="0" x2="1" y2="1">
        <stop offset="0" stop-color="#f4f4f4"/>
        <stop offset="1" stop-color="#ffffff"/>
      </linearGradient>
      <linearGradient id="frontBand" x1="0" y1="0" x2="1" y2="0">
        <stop offset="0" stop-color="#a10a10"/>
        <stop offset="0.55" stop-color="#c2050c"/>
        <stop offset="1" stop-color="#8c0a10"/>
      </linearGradient>
      <linearGradient id="frontPhoto" x1="0" y1="0" x2="1" y2="0">
        <stop offset="0" stop-color="#b79b7c"/>
        <stop offset="0.5" stop-color="#e7e4df"/>
        <stop offset="1" stop-color="#c9b8a2"/>
      </linearGradient>
    </defs>
    <rect width="764" height="519" fill="url(#frontPaper)"/>
    <path d="M442,0 C350,90 338,300 440,440 L764,440 L764,0 Z" fill="var(--red)"/>
    <path d="M458,0 C372,90 360,300 456,440 L764,440 L764,0 Z" fill="var(--silver)"/>
    <g role="img" aria-label="Photo of two doctors reviewing a patient chart in a clinic hallway">
      <path d="M470,0 C386,90 374,300 468,440 L764,440 L764,0 Z" fill="url(#frontPhoto)"/>
    </g>
    <path d="M0,371 Q420,480 764,283 L764,519 L0,519 Z" fill="var(--silver-dark)"/>
    <path d="M0,376 Q420,492 764,292 L764,519 L0,519 Z" fill="#dcdcdc"/>
    <path d="M0,382 Q420,500 764,304 L764,519 L0,519 Z" fill="url(#frontBand)"/>
  </svg>

  <div class="brand"><span class="brand-mark"></span>Dhelpit T Dunwat, M.D.</div>
  <div class="brand-tag">A Primary Care Office</div>

  <h1 class="headline">
    <div class="headline-lead">A healthy <strong>reminder,</strong></div>
    <div class="headline-lead">It is time for your</div>
    <div class="headline-big">annual</div>
    <div class="headline-big red">exam.</div>
  </h1>

  <div class="address">
    <svg width="12" height="17" viewBox="0 0 12 17" aria-hidden="true">
      <circle cx="6" cy="5.5" r="4" fill="none" stroke="#fff" stroke-width="1.6"/>
      <path d="M6,9.5 L6,14 M2,15.5 L10,15.5" stroke="#fff" stroke-width="1.6"/>
    </svg>
    <div>4820 N. Marlow Street Suite 210<br>Fresno, Ca 93711</div>
  </div>

  <div class="contact">
    <div class="contact-phone">
      <svg width="30" height="30" viewBox="0 0 30 30" aria-hidden="true">
        <circle cx="15" cy="15" r="13" fill="none" stroke="#fff" stroke-width="2"/>
        <path d="M10,8 L13,8 L14,12 L12,13.5 C13,16 14,17 16.5,18 L18,16 L22,17 L22,20 C22,21 21,22 20,22 C14,21.5 8.5,16 8,10 C8,9 9,8 10,8 Z" fill="#fff"/>
      </svg>
      (555) 014-2288
    </div>
    <div class="contact-web">
      <svg width="18" height="18" viewBox="0 0 18 18" aria-hidden="true" fill="none" stroke="#fff" stroke-width="1.4">
        <circle cx="9" cy="9" r="7.5"/>
        <ellipse cx="9" cy="9" rx="3.3" ry="7.5"/>
        <path d="M1.5,9 H16.5 M3,5 H15 M3,13 H15"/>
      </svg>
      <span>www.<strong>dhelpitdunwatmd</strong>.com</span>
    </div>
  </div>
</section>

<section class="card card-back">
  <svg class="card-shapes" viewBox="0 0 764 520" aria-hidden="true">
    <defs>
      <linearGradient id="backBuilding" x1="0" y1="0" x2="1" y2="0">
        <stop offset="0" stop-color="#8f8a80"/>
        <stop offset="0.5" stop-color="#4b4a46"/>
        <stop offset="1" stop-color="#5d6b4a"/>
      </linearGradient>
      <linearGradient id="backMap" x1="0" y1="0" x2="1" y2="0">
        <stop offset="0" stop-color="#d9e3d2"/>
        <stop offset="0.45" stop-color="#e6e6e6"/>
        <stop offset="1" stop-color="#ebebeb"/>
      </linearGradient>
    </defs>
    <rect width="764" height="520" fill="var(--mist)"/>
    <g role="img" aria-label="Street map showing the clinic location">
      <rect x="0" y="118" width="430" height="164" fill="url(#backMap)"/>
    </g>
    <path d="M0,282 L254,282 L275,358 L0,358 Z" fill="var(--red)"/>
    <path d="M254,282 L430,282 L430,358 L275,358 Z" fill="#121212"/>
    <g role="img" aria-label="Photo of the clinic building entrance">
      <rect x="0" y="358" width="430" height="162" fill="url(#backBuilding)"/>
    </g>
    <path d="M282,0 Q470,260 274,520 L764,520 L764,0 Z" fill="var(--silver-dark)"/>
    <path d="M300,0 Q484,260 290,520 L764,520 L764,0 Z" fill="var(--red)"/>
    <path d="M340,0 Q510,260 330,520 L764,520 L764,0 Z" fill="var(--paper)"/>
  </svg>

  <h2 class="doctors">Dr.'s Dhelpit <span>and</span><br>Sirel dunwat</h2>

  <div class="cta">CALL NOW<br>(555) 014-2288</div>

  <div class="social">
    <div class="social-line">VISIT US ON <span class="social-dot"></span></div>
    <div class="social-note">Located On The<br>Se Corner Of Marlow St</div>
  </div>

  <div class="stamp"></div>
  <div class="address-line" style="top:277px"></div>
  <div class="address-line" style="top:323px"></div>
  <div class="address-line" style="top:369px"></div>
</section>

</body>
</html>
```